Vantro cards

I am in the auto motive, transportation business I would like a business card that is Something cool, modern edgy, having to do with car culture. I offer towing service for high and exotic cars. I also provide towing for collisions and car accidents. I offer open and enclosed transport nationwide.

Target Market(s)

Car culture people high end auto collectors

Industry/Entity Type

Towing car carrier

Contact Information for Business Card

My company colors black yellow and silver

Font styles to use
Serif

```html
<!DOCTYPE html>
<html lang="en">
<head>
<meta charset="utf-8">
<title>Vantro cards</title>
<link href="https://fonts.googleapis.com/css2?family=Arimo:wght@400;700&display=swap" rel="stylesheet">
<style>
  :root {
    --bg: #e9e9e9;
    --card: #313131;
    --card-art: #3d3d3d;
    --yellow: #f2d43f;
    --white: #ffffff;
    --silver: #d8d8d8;
  }
  * { box-sizing: border-box; margin: 0; padding: 0; }
  html, body { width: 1200px; height: 802px; overflow: hidden; }
  body {
    background: var(--bg);
    font-family: "Arimo", Arial, sans-serif;
    display: flex;
    align-items: center;
    justify-content: center;
    gap: 40px;
  }
  .card {
    position: relative;
    width: 540px;
    height: 309px;
    background: var(--card);
    overflow: hidden;
    box-shadow: 0 10px 24px rgba(0,0,0,0.18);
  }
  .card-art {
    position: absolute;
    background: linear-gradient(135deg, var(--card-art), #383838);
    border-radius: 40px 120px 20px 20px;
  }
  .front .card-art { left: 260px; top: 80px; width: 240px; height: 150px; }
  .back .card-art { left: 30px; top: 120px; width: 470px; height: 180px; }

  .front-tab {
    position: absolute; top: 0; right: 0;
    width: 44px; height: 18px;
    background: var(--yellow);
  }
  .edge-band {
    position: absolute; left: 0; bottom: 0;
    width: 100%; height: 6px;
    display: flex;
  }
  .edge-band .band-yellow { flex: 0 0 62%; background: var(--yellow); }
  .edge-band .band-white { flex: 1; background: var(--white); }
  .back .edge-band { background: var(--yellow); }

  .identity {
    position: absolute; top: 30px; right: 40px;
    text-align: right;
  }
  .identity .person-name {
    color: var(--yellow); font-weight: 700; font-size: 19px; letter-spacing: 0.5px;
  }
  .identity .person-role {
    color: var(--silver); font-size: 13px; margin-top: 3px;
  }
  .address {
    position: absolute; right: 40px; top: 150px;
    text-align: right; color: var(--silver); font-size: 13px; line-height: 1.45;
  }

  .brand {
    position: absolute;
    display: flex; align-items: center; gap: 10px;
  }
  .brand-square { width: 18px; height: 18px; background: var(--yellow); }
  .brand-name {
    color: var(--white); font-weight: 700; font-size: 28px; letter-spacing: 2px;
  }
  .front .brand { left: 34px; top: 118px; }
  .back .brand { right: 40px; top: 50px; }

  .contacts {
    position: absolute; left: 34px; bottom: 34px;
    list-style: none; color: var(--silver); font-size: 13px;
  }
  .contacts li { display: flex; align-items: center; gap: 9px; margin-top: 7px; }
  .contacts svg { width: 13px; height: 13px; flex: none; }
</style>
</head>
<body>
  <section class="card front">
    <div class="card-art" role="img" aria-label="Faint flatbed tow truck illustration"></div>
    <div class="front-tab"></div>
    <div class="identity">
      <p class="person-name">MARCUS HALE</p>
      <p class="person-role">Manager</p>
    </div>
    <p class="address">Your Address, City<br>State, Zip 0000</p>
    <div class="brand">
      <span class="brand-square"></span>
      <span class="brand-name">VANTRO</span>
    </div>
    <ul class="contacts">
      <li>
        <svg viewBox="0 0 16 16"><path fill="#f2d43f" d="M3 1l3 3-2 2c1 2 3 4 5 5l2-2 3 3-2 3C7 15 1 9 0 4z"/></svg>
        555-013-4782
      </li>
      <li>
        <svg viewBox="0 0 16 16"><rect x="1" y="3" width="14" height="10" fill="#f2d43f"/><path d="M1 3l7 6 7-6" fill="none" stroke="#313131" stroke-width="1.5"/></svg>
        youremail@mailbox.com
      </li>
      <li>
        <svg viewBox="0 0 16 16"><circle cx="8" cy="8" r="7" fill="#f2d43f"/><circle cx="8" cy="8" r="3" fill="#313131"/></svg>
        www.vantrohaul.com
      </li>
    </ul>
    <div class="edge-band"><span class="band-yellow"></span><span class="band-white"></span></div>
  </section>

  <section class="card back">
    <div class="card-art" role="img" aria-label="Large faint flatbed tow truck illustration"></div>
    <div class="brand">
      <span class="brand-square"></span>
      <span class="brand-name">VANTRO</span>
    </div>
    <div class="edge-band"></div>
  </section>
</body>
</html>
```